Book Cover

Hello!
I need someone to design a book cover with the title, subtitle and one of the photos attached.

- Title: Walking Past Winter - By Corwin Haskett
- Subtitle: A Practical Path to living a calm and joyful life after treatment.

```html
<!DOCTYPE html>
<html lang="en">
<head>
<meta charset="utf-8">
<title>Walking Past Winter — Book Cover</title>
<link href="https://fonts.googleapis.com/css2?family=Anton&family=Oswald:wght@600&display=swap" rel="stylesheet">
<style>
  :root {
    --backdrop: #c2652a;
    --cover-yellow-top: #e0d50e;
    --cover-yellow-mid: #e6c205;
    --cover-yellow-bottom: #e9a800;
    --flame-red: #d9262b;
    --flame-orange: #e07a2c;
    --portrait-grey: #8c8a86;
    --jacket-blue: #2b4390;
    --jacket-navy: #1d2c63;
    --text-light: #f4f1ec;
  }
  html, body {
    margin: 0;
    width: 1200px;
    height: 800px;
    overflow: hidden;
    background: var(--backdrop);
  }
  .canvas {
    position: relative;
    width: 1200px;
    height: 800px;
  }
  .book-cover {
    position: absolute;
    left: 351px;
    top: 20px;
    width: 498px;
    height: 760px;
    overflow: hidden;
    background: linear-gradient(180deg, var(--cover-yellow-top) 0%, var(--cover-yellow-mid) 50%, var(--cover-yellow-bottom) 100%);
  }
  .flame-area {
    position: absolute;
    left: 30px;
    top: 68px;
    width: 444px;
    height: 358px;
    border-radius: 45% 40% 45% 50%;
    background: radial-gradient(ellipse at 55% 30%, var(--flame-red) 0%, var(--flame-red) 40%, rgba(224, 122, 44, 0.85) 70%, rgba(224, 122, 44, 0) 100%);
  }
  .portrait-area {
    position: absolute;
    left: 61px;
    top: 366px;
    width: 403px;
    height: 394px;
    border-radius: 140px 140px 0 0;
    background: linear-gradient(180deg, var(--portrait-grey) 0%, #4a5a8a 35%, var(--jacket-blue) 60%, var(--jacket-navy) 100%);
  }
  .title {
    position: absolute;
    left: 0;
    width: 100%;
    top: 30px;
    margin: 0;
    text-align: center;
    font-family: "Anton", sans-serif;
    font-weight: 400;
    font-size: 47px;
    line-height: 1;
    text-transform: uppercase;
    color: var(--text-light);
  }
  .subtitle {
    position: absolute;
    left: 0;
    width: 100%;
    top: 90px;
    margin: 0;
    text-align: center;
    font-family: "Oswald", sans-serif;
    font-weight: 600;
    font-size: 28px;
    line-height: 44px;
    color: var(--text-light);
  }
  .subtitle span { display: block; }
  .author {
    position: absolute;
    left: 0;
    width: 100%;
    top: 704px;
    margin: 0;
    text-align: center;
    font-family: "Oswald", sans-serif;
    font-weight: 600;
    font-size: 20px;
    line-height: 30px;
    color: var(--text-light);
  }
</style>
</head>
<body>
<main class="canvas">
  <section class="book-cover">
    <div class="flame-area" role="img" aria-label="Illustration of flowing red and orange flames with a two-way signpost"></div>
    <div class="portrait-area" role="img" aria-label="Photo of the author, an older man in a blue jacket, smiling and looking upward"></div>
    <h1 class="title">Walking Past Winter</h1>
    <p class="subtitle">
      <span>A Practical Path to living</span>
      <span>a calm and joyful life</span>
      <span>after treatment.</span>
    </p>
    <p class="author">By Corwin Haskett</p>
  </section>
</main>
</body>
</html>
```